Marcus Delbridge Finance

Need a personal website advertising Equipment Finance,Business Finance,Commercial Finance, Construction Finance, Bridging Finance. Similar websites are www.corvalend.com.au / www.tarmivest.com.au / www.qbr7.com.au /wwwhalvecredit.com.au

Target Market(s)

Business People

Industry/Entity Type

Business

Number of Pages Required

3 page

Font styles to use
Serif
Sans Serif

Requirements
Must have
• All i want is a simple corporate looking website advertising Equipment Finance, Commercial Finance, Construction Finance, Business Finance, Bridging Finance,

```html
<!DOCTYPE html>
<html lang="en">
<head>
<meta charset="utf-8">
<title>Marcus Delbridge Finance – The Business</title>
<link rel="stylesheet" href="https://fonts.googleapis.com/css2?family=Montserrat:wght@300;400&display=swap">
<style>
:root{
  --top-blue:#0d77ad;
  --nav-blue:#125f86;
  --accent:#29aee3;
  --heading:#1b6a97;
  --ink:#2b2b2b;
  --muted:#8a8a8a;
  --rule:#1a5e80;
  --field:#e6e6e6;
  --line:#e4e4e4;
  --icon-grey:#b9b9b9;
}
*{box-sizing:border-box;margin:0;padding:0}
html,body{width:1177px;height:1200px;overflow:hidden;background:#fff}
body{position:relative;font-family:"Montserrat",sans-serif;font-weight:300;color:var(--ink)}
.topbar{position:absolute;left:0;top:0;width:1177px;height:42px;background:var(--top-blue);color:#fff;font-size:12px;font-weight:400}
.topbar .links{position:absolute;left:68px;top:14px}
.topbar .phone{position:absolute;left:621px;top:14px}
.social{position:absolute;display:flex;gap:4px}
.topbar .social{left:1024px;top:11px}
.social span{display:block;width:18px;height:18px;border-radius:50%;background:#fff}
.brand{position:absolute;left:68px;top:66px;display:flex;align-items:center;gap:14px;font-size:32px;font-weight:400;color:#111}
.brand .mark{width:36px;height:36px;border-radius:50%;background:#111}
.search{position:absolute;left:618px;top:61px;width:322px;height:45px;background:var(--field);border-radius:2px}
.search svg{position:absolute;right:16px;top:12px}
.quote{position:absolute;left:955px;top:61px;width:154px;height:45px;background:var(--accent);color:#fff;font-size:17px;font-weight:400;display:flex;align-items:center;justify-content:center;border-radius:2px}
.nav{position:absolute;left:0;top:130px;width:1177px;height:53px;background:var(--nav-blue);display:flex}
.nav a{flex:1;display:flex;align-items:center;justify-content:center;color:#fff;text-decoration:none;font-size:17px;border-right:1px solid rgba(255,255,255,.55)}
.nav a:first-child{flex:0 0 217px;padding-left:34px}
.nav a:last-child{border-right:0}
.nav a.current{color:var(--accent)}
.crumbs{position:absolute;left:68px;top:197px;font-size:14px;color:var(--muted)}
.intro{position:absolute;left:328px;top:252px;display:flex;align-items:center;gap:26px}
.intro .badge{width:60px;height:62px;border-radius:50%;background:#111}
.intro h1{font-size:25px;font-weight:300;color:var(--heading)}
.copy{position:absolute;left:68px;top:368px;width:457px;font-size:18px;line-height:25px;text-align:justify;color:#333}
.copy p{margin-bottom:25px}
.team-photo{position:absolute;left:604px;top:368px;width:505px;height:395px;background:linear-gradient(135deg,#dfe6ee 0%,#c7d0db 45%,#4a4c55 100%)}
.divider{position:absolute;left:68px;top:887px;width:1041px;height:3px;background:var(--rule)}
.pay-label{position:absolute;left:68px;top:943px;font-size:12px;font-weight:400}
.pay-badge{position:absolute;left:70px;top:980px;width:160px;height:42px;border:1px solid #ddd;border-radius:2px;display:flex;align-items:center;gap:6px;padding-left:12px}
.pay-badge i{display:block;width:30px;height:16px;border-radius:2px;background:#1f4e92}
.pay-badge i:nth-child(2){background:#e84a2a;border-radius:8px}
.pay-badge i:nth-child(3){background:#2d83c6;width:20px}
.pay-badge i:nth-child(4){background:#cfd8e6;width:24px}
.contact{position:absolute;left:295px;font-size:12px;line-height:17px;color:#444}
.contact svg{position:absolute;left:0;top:0}
.contact p{margin-left:35px}
.foot-nav{position:absolute;right:68px;top:946px;display:flex;gap:18px;font-size:12px;font-weight:400;color:#333}
.foot-nav span:first-child{color:var(--muted);font-weight:300}
.foot-sub{position:absolute;right:68px;top:976px;font-size:12px;font-weight:400;color:#333;white-space:pre}
.foot-rule{position:absolute;left:0;top:1088px;width:1177px;height:1px;background:var(--line)}
.legal{position:absolute;left:68px;top:1119px;font-size:12px;font-weight:400;line-height:25px}
.follow{position:absolute;left:916px;top:1128px;font-size:12px;font-weight:400}
.follow-icons{left:995px;top:1121px;gap:5px}
.follow-icons span{width:24px;height:24px;background:var(--icon-grey)}
</style>
</head>
<body>
<header class="topbar">
  <span class="links">E-Book - Downloads Sitemap</span>
  <span class="phone">T: 1300 555 018</span>
  <div class="social" aria-label="Social links"><span></span><span></span><span></span><span></span></div>
</header>

<div class="brand"><span class="mark"></span>Marcus Delbridge Finance</div>
<div class="search">
  <svg width="22" height="22" viewBox="0 0 22 22"><rect width="22" height="22" rx="4" fill="#29aee3"/><circle cx="10" cy="10" r="5" fill="none" stroke="#fff" stroke-width="2"/><line x1="13.5" y1="13.5" x2="17" y2="17" stroke="#fff" stroke-width="2.4" stroke-linecap="round"/></svg>
</div>
<a class="quote">Quote Now</a>

<nav class="nav">
  <a>Home</a><a class="current">The Business</a><a>Key People</a><a>Products</a><a>Investors</a><a>Contact Us</a><a>Privacy</a>
</nav>

<div class="crumbs">Home / Business</div>

<div class="intro"><span class="badge"></span><h1>Know About the business and talk with us!</h1></div>

<section class="copy">
  <p>Lorem ipsum dolor sit amet, consectetuer adipiscing elit. Aenean commodo ligula eget dolor. Aenean massa. Cum sociis natoque penatibus et magnis dis parturient montes, nascetur ridiculus mus. Donec quam felis, ultricies nec, pellentesque eu, pretium quis, sem. Nulla consequat massa quis enim.</p>
  <p>Donec pede justo, fringilla vel, aliquet nec, vulputate eget, arcu. In enim justo, rhoncus ut, imperdiet a, venenatis vitae, justo. Nullam dictum felis eu pede mollis pretium. Integer tincidunt. Cras dapibus. Vivamus elementum semper nisi. Aenean vulputate eleifend tellus. Aenean leo ligula, porttitor eu, consequat vitae, eleifend ac, enim.</p>
  <p>Aliquam lorem ante, dapibus in, viverra quis, feugiat a, tellus.</p>
</section>

<div class="team-photo" role="img" aria-label="Photo of the finance team standing together in a bright office"></div>

<div class="divider"></div>

<footer>
  <div class="pay-label">Payments</div>
  <div class="pay-badge" aria-label="Accepted payment methods"><i></i><i></i><i></i><i></i></div>

  <div class="contact" style="top:946px">
    <svg width="16" height="20" viewBox="0 0 16 20"><path d="M8 0a7 7 0 0 0-7 7c0 5 7 13 7 13s7-8 7-13a7 7 0 0 0-7-7z" fill="#111"/><circle cx="8" cy="7" r="2.5" fill="#fff"/></svg>
    <p>214 Larkspur Drive,<br>Coral Bay, Queensland, 4210</p>
  </div>
  <div class="contact" style="top:996px">
    <svg width="22" height="22" viewBox="0 0 22 22"><circle cx="11" cy="11" r="9.5" fill="none" stroke="#111" stroke-width="2"/><path d="M11 5v6h4" fill="none" stroke="#111" stroke-width="2"/></svg>
    <p>Mon – Fri 9:00am – 5:00pm<br>Sat – Sun - Closed</p>
  </div>

  <div class="foot-nav"><span>Home</span><span>The Business</span><span>Key People</span><span>Products</span><span>Investors</span><span>Contact Us</span><span>Privacy</span></div>
  <div class="foot-sub">E-Book | Downloads Sitemap  |  Privacy Policy  | Sitemap</div>

  <div class="foot-rule"></div>
  <div class="legal">Secured by SSL<br>© 2017 Marcus Delbridge Finance</div>
  <div class="follow">Follow Us</div>
  <div class="social follow-icons"><span></span><span></span><span></span><span></span></div>
</footer>
</body>
</html>
```